Velvet Pressings Techno Label Business Card

I'm looking for a very clean business card for my Velvet Pressings music label. The label focusses on techno music. The card should include:

• my name : Tomas Brandt as "Founder & CEO"
• email address: tomas@velvet-pressings.example
• web: www.velvet-pressings.example
• facebook logo + /velvetpress
• twitter logo + /velvetpress
• soundcloud logo + /velvetpressings

Feel free to include your ideas! I'm looking forward to discuss about it.

Tomas

Industry/Entity Type

Business

Contact Information for Business Card

I don't like glossy cards. Prefer matt.

Requirements
Nice to have
• Maybe on one side the complete logo, other side just the icon.
Should not have
• Flashy stuff. Must be clean and business like style.

```html
<!DOCTYPE html>
<html lang="en">
<head>
<meta charset="utf-8">
<title>Velvet Pressings – Business Card</title>
<link rel="stylesheet" href="https://fonts.googleapis.com/css2?family=Arimo:wght@400;700&family=Saira:wght@400;600&display=swap">
<style>
  :root {
    --backdrop: #e4e4e2;
    --paper: #f7f7f6;
    --paper-shade: #ececeb;
    --slate: #8a8b8d;
    --ink: #6b6c6f;
    --accent: #f26b1d;
    --white: #ffffff;
  }
  * { margin: 0; padding: 0; box-sizing: border-box; }
  html, body { width: 1200px; height: 900px; overflow: hidden; }
  body {
    background: var(--backdrop);
    display: flex;
    flex-direction: column;
    align-items: center;
    justify-content: center;
    gap: 40px;
    font-family: "Saira", "Arial", sans-serif;
  }
  .card {
    position: relative;
    width: 700px;
    height: 400px;
    background: linear-gradient(160deg, var(--white) 0%, var(--paper) 55%, var(--paper-shade) 100%);
    box-shadow: 0 6px 18px rgba(0,0,0,0.12);
    overflow: hidden;
  }
  .brand {
    display: flex;
    align-items: center;
    gap: 14px;
  }
  .brand-dot {
    width: 34px; height: 34px;
    border-radius: 50%;
    background: var(--accent);
    flex: none;
  }
  .brand-name {
    font-family: "Arimo", "Arial", sans-serif;
    font-weight: 700;
    font-size: 40px;
    letter-spacing: -1px;
    color: var(--ink);
    white-space: nowrap;
  }
  /* back side */
  .card-back .brand {
    position: absolute;
    left: 50%; top: 50%;
    transform: translate(-50%, -50%);
  }
  /* front side */
  .card-front .sweep { position: absolute; inset: 0; }
  .card-front .brand { position: absolute; left: 56px; top: 70px; }
  .contact {
    position: absolute;
    right: 30px;
    top: 140px;
    list-style: none;
    color: var(--white);
    font-size: 14px;
    line-height: 1.25;
    text-align: right;
  }
  .contact li {
    display: flex;
    justify-content: flex-end;
    align-items: center;
    gap: 8px;
    height: 22px;
    white-space: nowrap;
  }
  .contact .address {
    display: block;
    height: auto;
    margin-bottom: 8px;
    padding-right: 22px;
  }
  .contact svg { width: 14px; height: 14px; flex: none; }
  .contact .social { gap: 6px; font-size: 13px; }
  .social-mark {
    width: 8px; height: 8px;
    border-radius: 50%;
    background: var(--accent);
    flex: none;
    margin-left: 8px;
  }
  .social-mark:first-child { margin-left: 0; }
  .holder {
    position: absolute;
    left: 300px;
    bottom: 28px;
  }
  .holder-name {
    font-weight: 600;
    font-size: 19px;
    letter-spacing: 1px;
    text-transform: uppercase;
    color: var(--accent);
  }
  .holder-role {
    font-size: 16px;
    color: var(--white);
  }
</style>
</head>
<body>

  <section class="card card-back" aria-label="Card back">
    <div class="brand">
      <span class="brand-dot"></span>
      <span class="brand-name">Velvet Pressings</span>
    </div>
  </section>

  <section class="card card-front" aria-label="Card front">
    <svg class="sweep" viewBox="0 0 700 400" width="700" height="400" aria-hidden="true">
      <path d="M120 400 C180 255 330 105 650 38 C340 118 200 262 150 400 Z" fill="var(--accent)"/>
      <path d="M165 400 C225 258 370 112 690 48 C380 126 240 266 185 400 Z" fill="var(--accent)"/>
      <path d="M200 400 C260 260 400 120 700 60 L700 400 Z" fill="var(--slate)"/>
    </svg>

    <div class="brand">
      <span class="brand-dot"></span>
      <span class="brand-name">Velvet Pressings</span>
    </div>

    <ul class="contact">
      <li class="address">14 Foundry Lane, Unit 4<br>Dockside Quarter DKQ</li>
      <li>020 555 0147
        <svg viewBox="0 0 16 16" aria-hidden="true"><path d="M3 1.5l3 .5 1 3-2 1.5a9 9 0 0 0 4.5 4.5L11 9l3 1 .5 3-2 1.5C7 14 2 9 1.5 3.5z" fill="var(--white)"/></svg>
      </li>
      <li>020 555 0148
        <svg viewBox="0 0 16 16" aria-hidden="true"><rect x="4" y="1" width="8" height="14" rx="1.5" fill="none" stroke="var(--white)" stroke-width="1.5"/><circle cx="8" cy="12.5" r="1" fill="var(--white)"/></svg>
      </li>
      <li>020 555 0149
        <svg viewBox="0 0 16 16" aria-hidden="true"><rect x="1" y="6" width="14" height="8" rx="1" fill="var(--white)"/><rect x="4" y="1" width="8" height="5" fill="none" stroke="var(--white)" stroke-width="1.5"/></svg>
      </li>
      <li>tomas@velvet-pressings.example
        <svg viewBox="0 0 16 16" aria-hidden="true"><rect x="1" y="3" width="14" height="10" rx="1" fill="var(--white)"/><path d="M1.5 3.5L8 9l6.5-5.5" fill="none" stroke="var(--slate)" stroke-width="1.3"/></svg>
      </li>
      <li>www.velvet-pressings.example
        <svg viewBox="0 0 16 16" aria-hidden="true"><circle cx="8" cy="8" r="6.5" fill="none" stroke="var(--white)" stroke-width="1.4"/><ellipse cx="8" cy="8" rx="3" ry="6.5" fill="none" stroke="var(--white)" stroke-width="1.2"/><path d="M1.5 8h13" stroke="var(--white)" stroke-width="1.2"/></svg>
      </li>
      <li class="social">
        <span class="social-mark"></span>/velvetpress
        <span class="social-mark"></span>/velvetpress
        <span class="social-mark"></span>/velvetpressings
      </li>
    </ul>

    <div class="holder">
      <p class="holder-name">Tomas Brandt</p>
      <p class="holder-role">Founder &amp; CEO</p>
    </div>
  </section>

</body>
</html>
```